Satchel & Sundial needs new business card design

I need a new business card design. I'm looking for out-of-the-box design which represents the freedom of being a location independent entrepreneur.
I offer coaching, retreats and trips.
I would like to see designs with and without the photo.
Colors I use are black (#000000), green (#25A796) and brown (#D7C38C)
Website satchelandsundial.example

Target Market(s)

location independent entrepreneurs, digital nomads, people looking to swap the 9 to 5 for a lifestyle business

Industry/Entity Type

Business

Contact Information for Business Card

Dorota Falkner
Your Lifestyle Business Coach, Retreat & Trip Leader
http://satchelandsundial.example
hello@satchelandsundial.example
Live a life you don't need a holiday from

Font styles to use
Serif
Sans Serif

Requirements
Must have
• One side should contain only the logo. I would also consider having the "Live a life you don't need a holiday from" on that side too (depending on how it looks)
• Please show both sides on the designs.

```html
<!DOCTYPE html>
<html lang="en">
<head>
<meta charset="utf-8">
<title>Satchel &amp; Sundial — Business Card</title>
<link rel="stylesheet" href="https://fonts.googleapis.com/css2?family=Quicksand:wght@500;700&family=Saira+Stencil+One&family=Oswald:wght@500&display=swap">
<style>
  :root {
    --ink: #000000;
    --ink-soft: #1d1d1d;
    --teal: #25a796;
    --gold: #d7c38c;
    --gold-light: #e6d8ac;
    --gold-deep: #c9b57c;
    --paper: #ffffff;
    --backdrop: #e9e7e2;
    --foliage: #7d8a5c;
    --bark: #8a7a5a;
  }
  * { box-sizing: border-box; margin: 0; padding: 0; }
  html, body { width: 1200px; height: 900px; overflow: hidden; }
  body { background: var(--backdrop); position: relative; font-family: "Quicksand", sans-serif; }

  .card {
    position: absolute;
    width: 540px;
    height: 310px;
    border-radius: 22px;
    overflow: hidden;
    box-shadow: 0 10px 28px rgba(0,0,0,.18);
  }

  /* Front: logo side */
  .card--front { left: 80px; top: 140px; background: var(--paper); }
  .brand-name {
    position: absolute; left: 0; right: 0; top: 100px;
    text-align: center;
    font-family: "Quicksand", sans-serif; font-weight: 700;
    font-size: 40px; letter-spacing: 1px;
    color: var(--ink);
  }
  .tagline {
    position: absolute; left: 0; right: 0; bottom: 42px;
    text-align: center;
    font-weight: 700; font-size: 17px;
    color: var(--ink-soft);
  }

  /* Back: contact side */
  .card--back {
    left: 580px; top: 450px;
    background: linear-gradient(160deg, var(--gold-light) 0%, var(--gold) 45%, var(--gold-deep) 100%);
  }
  .portrait {
    position: absolute; left: 0; top: 70px; bottom: 0; width: 340px;
    background:
      radial-gradient(ellipse at 45% 55%, #f2efe8 0 12%, transparent 26%),
      linear-gradient(170deg, var(--foliage) 0%, var(--bark) 45%, #6f8a55 100%);
    -webkit-mask-image: linear-gradient(90deg, #000 55%, transparent 100%);
            mask-image: linear-gradient(90deg, #000 55%, transparent 100%);
  }
  .name-band {
    position: absolute; right: 0; top: 92px;
    width: 330px; height: 58px;
    background: var(--teal);
    clip-path: polygon(14px 0, 100% 0, 100% 100%, 0 100%);
    padding: 7px 0 0 30px;
  }
  .name {
    font-family: "Saira Stencil One", sans-serif;
    font-size: 27px; line-height: 1;
    letter-spacing: 4px;
    color: var(--gold-light);
  }
  .role {
    margin-top: 4px;
    font-family: "Oswald", sans-serif; font-weight: 500;
    font-size: 9.5px; letter-spacing: .6px;
    text-transform: uppercase;
    color: var(--gold-light);
  }
  .contact {
    position: absolute; right: 34px; top: 180px;
    font-weight: 700; font-size: 14px; line-height: 24px;
    color: var(--ink-soft);
    text-align: left;
  }
  .contact .accent { color: var(--teal); }
</style>
</head>
<body>

  <section class="card card--front" aria-label="Business card front">
    <div class="brand-name">Satchel &amp; Sundial</div>
    <p class="tagline">Live a life you don’t need a holiday from</p>
  </section>

  <section class="card card--back" aria-label="Business card back">
    <div class="portrait" role="img" aria-label="Photo of the coach sitting on a wooden fence among trees, holding a small sign"></div>
    <div class="name-band">
      <div class="name">DOROTA FALKNER</div>
      <div class="role">Your lifestyle business coach, retreat &amp; trip leader</div>
    </div>
    <div class="contact">
      <div>hello@satchelandsundial.example</div>
      <div>www.<span class="accent">satchelandsundial</span>.example</div>
    </div>
  </section>

</body>
</html>
```